"Kestrava Inc." Needs a Logo Design and Business Card

The name of the company is "Kestrava Inc."
Our Business decription, which should appear on the front of the Business Card along with the logo and business name is:
"Boutique Global Procurement and Management Services"
We offer the following SERVICES that should be listed on the back of the Business Card :
"Consultants"
"Management"
"Business Research & Development"
"Sourcing Agent"
"Distributors"
We would like to see designs that use the colors
burnt orange and,
stainless steel
Business card designs should be innovatively modern and contemporary
Telephone number and email address should be on the back of the card
The name of the firm is "Kestrava Inc.
Industry/Entity Type
Steel
Look and feel
Each slider illustrates characteristics of the customer's brand and the style your logo design should communicate.

```html
<!DOCTYPE html>
<html lang="en">
<head>
<meta charset="utf-8">
<title>Kestrava Inc. Business Card</title>
<link rel="stylesheet" href="https://fonts.googleapis.com/css2?family=Ubuntu:wght@400;500;700&family=Questrial&display=swap">
<style>
  :root {
    --burnt-orange: #d24d0e;
    --burnt-orange-deep: #c3410b;
    --steel: #8f8f8f;
    --ink: #2b2b2b;
    --paper: #f4f4f3;
    --backdrop: #555555;
    --tagline-on-orange: #eba07a;
    --text-on-orange: #ffffff;
  }
  * { margin: 0; padding: 0; box-sizing: border-box; }
  html, body { width: 1200px; height: 1000px; overflow: hidden; }
  body { background: var(--backdrop); position: relative; font-family: "Ubuntu", sans-serif; }

  .card {
    position: absolute;
    width: 530px;
    height: 302px;
    border-radius: 14px;
    overflow: hidden;
  }
  .card--front { left: 164px; top: 172px; background: var(--paper); }
  .card--back {
    left: 472px; top: 550px;
    background: linear-gradient(135deg, var(--burnt-orange) 0%, var(--burnt-orange-deep) 100%);
  }

  .accent-tab { position: absolute; left: 0; top: 60px; width: 13px; height: 67px; }
  .card--front .accent-tab { background: var(--burnt-orange); }
  .card--back .accent-tab { top: 54px; width: 14px; height: 68px; background: #ffffff; }

  .steel-band { position: absolute; right: 0; bottom: 0; height: 14px; background: var(--steel); }
  .card--front .steel-band { left: 240px; }
  .card--back .steel-band { left: 246px; }

  .brand { position: absolute; }
  .card--front .brand { left: 239px; top: 56px; }
  .card--back .brand { left: 245px; top: 48px; }

  .brand-name {
    font-family: "Ubuntu", sans-serif;
    font-weight: 500;
    font-size: 32px;
    line-height: 36px;
  }
  .card--front .brand-name { color: var(--burnt-orange); }
  .card--back .brand-name { color: var(--text-on-orange); }

  .tagline { margin-top: 4px; font-size: 13px; line-height: 17px; }
  .card--front .tagline { color: var(--ink); }
  .card--back .tagline { color: var(--tagline-on-orange); }

  .person {
    position: absolute;
    right: 324px;
    top: 198px;
    text-align: right;
    font-family: "Questrial", sans-serif;
    color: var(--ink);
  }
  .person-name { font-family: "Ubuntu", sans-serif; font-weight: 700; font-size: 15px; line-height: 18px; letter-spacing: 0.5px; }
  .person-role { font-size: 13px; line-height: 17px; }

  .address {
    position: absolute;
    left: 240px;
    top: 198px;
    font-family: "Questrial", sans-serif;
    font-style: normal;
    font-size: 12.5px;
    line-height: 15px;
    color: var(--ink);
  }

  .services {
    position: absolute;
    left: 40px;
    top: 150px;
    list-style: none;
    font-family: "Questrial", sans-serif;
    font-size: 12.5px;
    line-height: 17px;
    color: var(--text-on-orange);
  }
  .services-title {
    font-family: "Ubuntu", sans-serif;
    font-weight: 700;
    font-size: 13px;
    letter-spacing: 0.5px;
    margin-bottom: 3px;
    color: var(--text-on-orange);
  }
  .services-block { position: absolute; left: 40px; top: 150px; }
  .services-block .services { position: static; }

  .contact {
    position: absolute;
    left: 245px;
    top: 170px;
    list-style: none;
    font-family: "Questrial", sans-serif;
    font-size: 12.5px;
    line-height: 17px;
    color: var(--text-on-orange);
  }
  .contact-label { color: var(--tagline-on-orange); }
</style>
</head>
<body>
  <section class="card card--front" aria-label="Business card front">
    <div class="accent-tab"></div>
    <div class="brand">
      <div class="brand-name">KESTRAVA Inc.</div>
      <div class="tagline">Boutique Global Procurement<br>and Management Services</div>
    </div>
    <div class="person">
      <div class="person-name">MARTIN HALE</div>
      <div class="person-role">Sales Manager</div>
    </div>
    <address class="address">
      28 Harbour Parade<br>
      Avoca NSW 2251
    </address>
    <div class="steel-band"></div>
  </section>

  <section class="card card--back" aria-label="Business card back">
    <div class="accent-tab"></div>
    <div class="brand">
      <div class="brand-name">KESTRAVA Inc.</div>
      <div class="tagline">Boutique Global Procurement<br>and Management Services</div>
    </div>
    <div class="services-block">
      <div class="services-title">SERVICES</div>
      <ul class="services">
        <li>Consultants</li>
        <li>Management</li>
        <li>Business Research &amp; Development</li>
        <li>Sourcing Agent</li>
        <li>Distributors</li>
      </ul>
    </div>
    <ul class="contact">
      <li><span class="contact-label">Phone:</span> 0412 555 019</li>
      <li><span class="contact-label">Email:</span> martin@kestrava.com</li>
    </ul>
    <div class="steel-band"></div>
  </section>
</body>
</html>
```